Keystonery Billboard - Financial Services Company (Investments, Tax Planning and Insurance)

Our new office has a billboard directly above the office building. We'd like something eye-catching with a strong Call to Action, with the main part of the billboard being under 7 words if possible. We'd like you to include a way to get ahold of us (either our website keystoneryllc.example or our phone number 302-418-2907. You may also include in small font something to indicate that we've been serving the area since 1980 (the DE area, the tri-state area, the Marlowe Hollow, etc.)

We offer financial planning, tax planning, and insurance, and we help our clients to focus on their goals and happiness by providing everything they need for lifelong wealth under one roof.

Our logos are attached, we use a triangle logo with green and gray. We use the tagline "discover lasting prosperity" but this does not need to be included.

Potential ideas we have seen from other financial companies-
- the concept that the driver spends more time looking at billboards than planning for their retirement
-something along the lines of "everything you need for your finances is in this building right here" planning, investments, taxes, insurance"
-don't spend your time worrying about retirement, let us help you plan for it
-are you working for your money, or is it working for you?
- retirement takes planning, we're here to help
- ready to retire? talk to us
- need investment advice?
- need help investing?
- crossing your fingers isn't a retirement plan. we can help.
- retiring soon? you need help.

Those are just general ideas, please feel free to be creative.

brand colors:
#00b585
#00b185
#000000
#ffffff
#6d6f75
#6d6f75
#6f7074
#021712
#052e24

```html
<!DOCTYPE html>
<html lang="en">
<head>
<meta charset="utf-8">
<title>Keystonery Billboard</title>
<link rel="stylesheet" href="https://fonts.googleapis.com/css2?family=Montserrat:wght@500;800&family=Tinos:wght@400;700&display=swap">
<style>
  :root {
    --green: #00935f;
    --green-bright: #00a06a;
    --green-deep: #0a5a43;
    --gray: #6d6f75;
    --gray-dark: #5e6066;
    --white: #ffffff;
    --backdrop: #e4e4e4;
  }
  * { margin: 0; padding: 0; box-sizing: border-box; }
  html, body { width: 1000px; height: 1200px; overflow: hidden; }
  body { background: var(--backdrop); position: relative; font-family: "Montserrat", sans-serif; }

  .billboard {
    position: absolute; left: 20px; top: 360px;
    width: 960px; height: 480px;
    background: var(--white); overflow: hidden;
  }
  .billboard__art { position: absolute; inset: 0; }

  .brand {
    position: absolute; left: 0; right: 0; top: 38px;
    text-align: center;
  }
  .brand__name {
    font-family: "Tinos", serif; font-weight: 400;
    font-size: 60px; line-height: 56px; color: var(--green);
    letter-spacing: -1px;
  }
  .brand__tagline {
    font-family: "Montserrat", sans-serif; font-weight: 500;
    font-size: 10.5px; letter-spacing: 4.6px; text-transform: uppercase;
    color: var(--gray); margin-top: 6px;
  }

  .headline { position: absolute; left: 42px; top: 196px; }
  .headline__lead {
    font-weight: 800; font-size: 38px; line-height: 40px;
    color: var(--gray); letter-spacing: -0.5px; text-transform: uppercase;
  }
  .headline__focus {
    font-weight: 800; font-size: 76px; line-height: 78px;
    color: var(--green); letter-spacing: -3px;
  }

  .services { position: absolute; inset: 0; list-style: none; }
  .service { position: absolute; display: flex; align-items: center; gap: 11px; }
  .service__icon { width: 40px; height: 40px; flex: none; }
  .service__label {
    font-family: "Tinos", serif; font-weight: 700;
    font-size: 22px; color: var(--gray);
  }
  .service--planning { left: 591px; top: 155px; }
  .service--investments { left: 644px; top: 211px; }
  .service--taxes { left: 698px; top: 267px; }
  .service--insurance { left: 751px; top: 323px; }

  .contact-bar {
    position: absolute; left: 0; right: 0; bottom: 0; height: 70px;
    background: linear-gradient(90deg, var(--green-deep) 0%, var(--green) 55%, var(--green-bright) 100%);
    display: flex; align-items: center; padding-left: 44px;
    color: var(--white); font-weight: 800;
  }
  .contact-bar__icon { width: 40px; height: 40px; flex: none; }
  .contact-bar__phone { font-size: 43px; margin-left: 8px; letter-spacing: -0.5px; }
  .contact-bar__divider {
    width: 3px; height: 42px; background: var(--white);
    margin: 0 16px 0 20px;
  }
  .contact-bar__web { font-size: 34px; margin-left: 10px; letter-spacing: -0.3px; }
</style>
</head>
<body>
  <main class="billboard">
    <svg class="billboard__art" width="960" height="480" viewBox="0 0 960 480">
      <defs>
        <linearGradient id="pyramid-green" x1="0" y1="0" x2="0" y2="1">
          <stop offset="0" stop-color="#00a56b"/>
          <stop offset="1" stop-color="#008e5a"/>
        </linearGradient>
        <linearGradient id="pyramid-gray" x1="0" y1="0" x2="1" y2="1">
          <stop offset="0" stop-color="#6d6f75"/>
          <stop offset="1" stop-color="#5b5d62"/>
        </linearGradient>
      </defs>
      <polygon class="pyramid pyramid--green" points="500,121 223,410 789,410" fill="url(#pyramid-green)"
               role="img" aria-label="Photo of a green tree growing from a pile of coins"/>
      <path class="pyramid pyramid--gray" d="M630 252 L776 410 L526 410 Q534 296 630 252 Z" fill="url(#pyramid-gray)"
            role="img" aria-label="Photo of gold coins on a gray floor"/>
      <path class="pyramid__divider" d="M622 250 Q528 296 518 412" fill="none" stroke="#ffffff" stroke-width="8"/>
    </svg>

    <header class="brand">
      <div class="brand__name">Keystonery</div>
      <div class="brand__tagline">Discover lasting prosperity</div>
    </header>

    <h1 class="headline">
      <span class="headline__lead" style="display:block">How's your</span>
      <span class="headline__focus" style="display:block">401(K)?</span>
    </h1>

    <ul class="services">
      <li class="service service--planning">
        <svg class="service__icon" viewBox="0 0 40 40" aria-hidden="true">
          <circle cx="20" cy="20" r="20" fill="var(--green)"/>
          <circle cx="20" cy="20" r="10" fill="none" stroke="#fff" stroke-width="1.5" stroke-dasharray="3 1.5"/>
          <circle cx="20" cy="20" r="6.5" fill="none" stroke="#fff" stroke-width="1.3"/>
          <text x="20" y="23.5" text-anchor="middle" font-size="9" font-family="Montserrat, sans-serif" font-weight="800" fill="#fff">$</text>
        </svg>
        <span class="service__label">Planning</span>
      </li>
      <li class="service service--investments">
        <svg class="service__icon" viewBox="0 0 40 40" aria-hidden="true">
          <circle cx="20" cy="20" r="20" fill="var(--green)"/>
          <circle cx="20" cy="14" r="6" fill="none" stroke="#fff" stroke-width="1.4"/>
          <text x="20" y="17.2" text-anchor="middle" font-size="8" font-family="Montserrat, sans-serif" font-weight="800" fill="#fff">$</text>
          <path d="M20 20 V29 M20 26 Q15 25 14 21 Q18 21 20 25 M20 25 Q22 21 26 21 Q25 25 20 26 M13 30 H27" fill="none" stroke="#fff" stroke-width="1.4" stroke-linecap="round"/>
        </svg>
        <span class="service__label">Investments</span>
      </li>
      <li class="service service--taxes">
        <svg class="service__icon" viewBox="0 0 40 40" aria-hidden="true">
          <circle cx="20" cy="20" r="20" fill="var(--green)"/>
          <rect x="11" y="10" width="14" height="19" fill="none" stroke="#fff" stroke-width="1.4"/>
          <text x="12.5" y="15.5" font-size="4.5" font-family="Montserrat, sans-serif" font-weight="800" fill="#fff">TAX</text>
          <path d="M13 19 H23 M13 22 H23 M13 25 H20" stroke="#fff" stroke-width="1.2"/>
          <rect x="22" y="20" width="8" height="10" fill="var(--green)" stroke="#fff" stroke-width="1.3"/>
          <path d="M24 23 H28 M24 25.5 H28 M24 28 H28" stroke="#fff" stroke-width="1"/>
        </svg>
        <span class="service__label">Taxes</span>
      </li>
      <li class="service service--insurance">
        <svg class="service__icon" viewBox="0 0 40 40" aria-hidden="true">
          <circle cx="20" cy="20" r="20" fill="var(--green)"/>
          <path d="M13 18 Q13 10 21 10 Q29 10 29 18 Z M21 10 V22" fill="none" stroke="#fff" stroke-width="1.4" stroke-linejoin="round"/>
          <path d="M9 27 L14 24 H20 Q22 24 21 26 H16 M21 26 L27 23 Q29 23 28 25 L20 30 H11" fill="none" stroke="#fff" stroke-width="1.4" stroke-linecap="round" stroke-linejoin="round"/>
        </svg>
        <span class="service__label">Insurance</span>
      </li>
    </ul>

    <footer class="contact-bar">
      <svg class="contact-bar__icon" viewBox="0 0 40 40" aria-hidden="true">
        <circle cx="20" cy="20" r="20" fill="#fff"/>
        <path d="M13 11 L17 10 L19 16 L16 18 Q18 23 22 25 L24 22 L30 24 L29 28 Q27 31 22 29 Q14 25 11 17 Q10 13 13 11 Z" fill="var(--green-deep)"/>
      </svg>
      <span class="contact-bar__phone">302-418-2907</span>
      <span class="contact-bar__divider"></span>
      <svg class="contact-bar__icon" viewBox="0 0 40 40" aria-hidden="true">
        <circle cx="20" cy="20" r="20" fill="#fff"/>
        <g fill="none" stroke="var(--green-deep)" stroke-width="1.6">
          <circle cx="20" cy="20" r="11"/>
          <ellipse cx="20" cy="20" rx="5" ry="11"/>
          <path d="M9 20 H31 M11 14.5 H29 M11 25.5 H29 M20 9 V31"/>
        </g>
      </svg>
      <span class="contact-bar__web">keystoneryllc.example</span>
    </footer>
  </main>
</body>
</html>
```